Consulting business card

*1) An Overview:* The business is simply a financial transaction wherein I
offer to provide advice to financial holders of commercial real estate
mortgages (which are sub-performing or non-performing), and said holders
are desirous of selling said mortgages which I will offer advice to said
holders in the purchase of said mortgages. Please note the attached copy
of a proposed line-by-line business card which starts with the 1st line
"RKW Advisory, LLC" with the 2nd line "Purchase of Commercial Mortgage
Loan" and the 3rd line "Sub-performing and Non-performing" is my desired
copy subject to any suggested changes. Please ignore the the copy below
the aforementioned proposed card/copy as it will be activated at a later
date.and advise
*2) The Target Market:* I contact and advise senior officers in banks,
insurance companies, and financial institutions such as CEOs, CFOs, COOs,
and Loan Mitigation Officers: the senior officers are tasked with the
removal of sub-performing and non-performing commercial real estate loans
from their real estate portfolios. The desired market is targeted at $1-10
million USD and located in the US.
*3) Design Specifics: *STYLE should be conservative and be representative
of the financial market contacts; COLOR might show a rich forest green
element, a gold foil accent, and subtle black printing, however,
alternatively, silver foil accent(s) with strong black print would seem in
harmony with the services offered, however, I would appreciate any artful
suggestions; IMAGERY should be subtle (no logo can be strong enough to make
an immediate impact): the quality should make the recipient feel he/she has
just met an experienced and competent financial adviser (I have over 55
years of successful financial and business experience).
720.217.6154davidfredrickjones@gmail.com

```html
<!DOCTYPE html>
<html lang="en">
<head>
<meta charset="utf-8">
<title>RKW Advisory, LLC — Business Card</title>
<link rel="stylesheet" href="https://fonts.googleapis.com/css2?family=Noto+Serif:wght@400;700&family=Arimo:wght@400&display=swap">
<style>
  :root {
    --backdrop: #1c1f1c;
    --card-gold: #9c8c3e;
    --card-gold-light: #a49545;
    --forest-dark: #1f4a26;
    --forest: #336636;
    --ink-light: #f1eee2;
    --rule: #ece8da;
  }
  html, body {
    margin: 0;
    padding: 0;
    width: 1200px;
    height: 800px;
    overflow: hidden;
    background: var(--backdrop);
  }
  .canvas {
    position: relative;
    width: 1200px;
    height: 800px;
  }
  .business-card {
    position: absolute;
    left: 180px;
    top: 160px;
    width: 840px;
    height: 480px;
    overflow: hidden;
    background: linear-gradient(160deg, var(--card-gold-light), var(--card-gold));
    box-shadow: 0 10px 30px rgba(0,0,0,0.5);
  }
  .edge-band {
    position: absolute;
    top: 0;
    right: 0;
    width: 96px;
    height: 480px;
    background: var(--forest-dark);
  }
  .edge-band-inner {
    position: absolute;
    top: 0;
    right: 96px;
    width: 14px;
    height: 480px;
    background: var(--forest);
  }
  .card-content {
    position: absolute;
    left: 0;
    top: 0;
    width: 730px;
    height: 480px;
    color: var(--ink-light);
  }
  .company-block {
    position: absolute;
    top: 50px;
    left: 0;
    width: 730px;
    text-align: center;
  }
  .company-name {
    margin: 0;
    font-family: "Noto Serif", Georgia, serif;
    font-weight: 400;
    font-size: 50px;
    letter-spacing: 0.5px;
    line-height: 1.1;
  }
  .company-tagline {
    margin: 6px 0 0;
    font-family: "Arimo", Arial, sans-serif;
    font-size: 22px;
    line-height: 1.3;
  }
  .divider {
    position: absolute;
    top: 210px;
    left: 0;
    width: 600px;
    height: 0;
    border-top: 1.5px solid var(--rule);
  }
  .contact-block {
    position: absolute;
    top: 244px;
    left: 0;
    width: 730px;
    text-align: center;
  }
  .person-name {
    margin: 0 0 16px;
    font-family: "Noto Serif", Georgia, serif;
    font-weight: 700;
    font-size: 32px;
    letter-spacing: 0.5px;
  }
  .contact-line {
    margin: 0;
    font-family: "Arimo", Arial, sans-serif;
    font-size: 20px;
    line-height: 1.5;
  }
</style>
</head>
<body>
<div class="canvas">
  <div class="business-card">
    <div class="edge-band-inner"></div>
    <div class="edge-band"></div>
    <div class="card-content">
      <div class="company-block">
        <h1 class="company-name">RKW Advisory, LLC</h1>
        <p class="company-tagline">Purchase of Commercial Mortgage Loan<br>Sub-performing and Non-performing</p>
      </div>
      <div class="divider"></div>
      <div class="contact-block">
        <p class="person-name">Glen Marlowe</p>
        <p class="contact-line">555.304.8827</p>
        <p class="contact-line">tomasheraldwick@mailbox.example</p>
      </div>
    </div>
  </div>
</div>
</body>
</html>
```